Velmora Systems Business Card Design

We need a new design for our IT Security and Management consulting business. we're based out of NY so NYC elements can (and should) be incorporated. We focus on financial services companies but aren't exclusive, so elements with financial services can be included as well. I'm looking for something clean and modern, a bit bold but nothing crazy and not busy.

Target Market(s)

Financial Services and Small Business

Industry/Entity Type

It Company

Contact Information for Business Card

Doran Kellewick
President/CTO
201-555-0143
dk@velmorasys.example
518 Thornbury Avenue
Suite 214-#35
Ashcombe, NJ 07999
www.velmorasys.example

Font styles to use
Serif
Sans Serif

Colors
f37122
ec1f27
3176b5

Requirements
Must have
• "white" space on one side. (doesn't actually have to be white). we plan to use Prelk.com which will have an orange middle edge between front and back. (see attached example). Logo attached.
Nice to have
• new york city scape

```html
<!DOCTYPE html>
<html lang="en">
<head>
<meta charset="utf-8">
<title>Velmora Systems Business Card</title>
<link href="https://fonts.googleapis.com/css2?family=Lato:wght@400;700;900&display=swap" rel="stylesheet">
<style>
  :root {
    --brand-blue: #3176b5;
    --deep-blue: #0d5fb0;
    --bright-blue: #1a8ad0;
    --brand-red: #ec1f27;
    --brand-orange: #f37122;
    --ink: #1d1d1d;
    --rule: #9a9a9a;
    --paper: #ffffff;
    --backdrop: #d6d6d6;
  }
  * { box-sizing: border-box; margin: 0; padding: 0; }
  html, body { width: 1200px; height: 1000px; overflow: hidden; }
  body {
    background: radial-gradient(ellipse at center, #eeeeee 0%, var(--backdrop) 100%);
    font-family: "Lato", Arial, sans-serif;
    position: relative;
  }
  .card {
    position: absolute;
    left: 250px;
    width: 700px;
    height: 400px;
    border-radius: 26px;
    overflow: hidden;
    box-shadow: 0 12px 30px rgba(0,0,0,0.25);
  }
  /* Front */
  .card-front { top: 70px; background: var(--paper); }
  .card-front .field {
    position: absolute; left: 0; right: 0; top: 44px; bottom: 44px;
    background: radial-gradient(ellipse at 70% 100%, var(--bright-blue) 0%, var(--deep-blue) 70%);
    display: flex; flex-direction: column; align-items: center; justify-content: center;
  }
  .front-brand { display: flex; align-items: center; gap: 18px; }
  .front-brand .mark { width: 46px; height: 46px; border-radius: 50%; background: var(--paper); flex: none; }
  .front-brand .name {
    color: var(--paper); font-weight: 900; font-size: 60px; letter-spacing: -0.5px; white-space: nowrap;
  }
  .front-tagline {
    color: var(--paper); font-weight: 700; font-size: 24px; margin-top: 6px; margin-left: 64px;
  }
  /* Back */
  .card-back { top: 530px; background: var(--paper); }
  .card-back .band {
    position: absolute; left: 0; right: 0; height: 40px; background: var(--deep-blue);
  }
  .card-back .band-top { top: 0; }
  .card-back .band-bottom { bottom: 0; }
  .identity {
    position: absolute; left: 40px; top: 120px; width: 330px; text-align: center;
  }
  .back-brand { display: flex; align-items: center; justify-content: center; gap: 10px; }
  .back-brand .mark { width: 26px; height: 26px; border-radius: 50%; background: var(--brand-orange); flex: none; }
  .back-brand .name { color: var(--brand-red); font-weight: 900; font-size: 32px; white-space: nowrap; }
  .back-tagline { color: var(--brand-orange); font-weight: 700; font-size: 13px; margin-top: 2px; margin-left: 36px; }
  .address { margin-top: 26px; color: var(--ink); font-size: 17px; line-height: 1.35; }
  .divider { position: absolute; left: 380px; top: 60px; }
  .contact { position: absolute; left: 420px; top: 76px; width: 250px; }
  .person { color: var(--brand-blue); font-weight: 700; font-size: 26px; white-space: nowrap; }
  .role { color: var(--brand-red); font-size: 15px; margin-top: 2px; }
  .rows { margin-top: 12px; list-style: none; }
  .rows li {
    display: flex; align-items: center; gap: 12px;
    padding: 8px 0; border-top: 1px solid var(--rule);
    font-size: 16px; color: var(--ink); white-space: nowrap;
  }
  .rows li:last-child { border-bottom: 1px solid var(--rule); }
  .icon { width: 26px; height: 26px; flex: none; }
</style>
</head>
<body>
  <section class="card card-front" aria-label="Card front">
    <div class="field">
      <div class="front-brand">
        <span class="mark"></span>
        <span class="name">Velmora Systems</span>
      </div>
      <div class="front-tagline">Insight Shield Clarity Daily</div>
    </div>
  </section>

  <section class="card card-back" aria-label="Card back">
    <div class="band band-top"></div>
    <div class="band band-bottom"></div>

    <div class="identity">
      <div class="back-brand">
        <span class="mark"></span>
        <span class="name">Velmora Systems</span>
      </div>
      <div class="back-tagline">Insight Shield Clarity Daily</div>
      <p class="address">518 Thornbury Avenue<br>Suite 214-#35, Ashcombe, NJ 07999</p>
    </div>

    <svg class="divider" width="40" height="280" viewBox="0 0 40 280" aria-hidden="true">
      <line x1="2" y1="2" x2="2" y2="278" stroke="#9a9a9a" stroke-width="1"/>
    </svg>

    <div class="contact">
      <div class="person">Doran Kellewick</div>
      <div class="role">President/CTO</div>
      <ul class="rows">
        <li>
          <svg class="icon" viewBox="0 0 26 26" aria-hidden="true">
            <circle cx="13" cy="13" r="13" fill="#3176b5"/>
            <path d="M9 7c1 0 2 2 2 3s-1 1-1 2 2 4 4 4 1-1 2-1 3 1 3 2-1 2-3 2c-4 0-9-5-9-9 0-2 1-3 2-3z" fill="#fff"/>
          </svg>
          201-555-0143
        </li>
        <li>
          <svg class="icon" viewBox="0 0 26 26" aria-hidden="true">
            <circle cx="13" cy="13" r="13" fill="#3176b5"/>
            <rect x="6.5" y="8.5" width="13" height="9" fill="none" stroke="#fff" stroke-width="1.5"/>
            <path d="M6.5 8.5 13 14l6.5-5.5" fill="none" stroke="#fff" stroke-width="1.5"/>
          </svg>
          dk@velmorasys.example
        </li>
        <li>
          <svg class="icon" viewBox="0 0 26 26" aria-hidden="true">
            <circle cx="13" cy="13" r="13" fill="#3176b5"/>
            <circle cx="13" cy="13" r="6.5" fill="none" stroke="#fff" stroke-width="1.5"/>
            <ellipse cx="13" cy="13" rx="2.8" ry="6.5" fill="none" stroke="#fff" stroke-width="1.2"/>
            <line x1="6.5" y1="13" x2="19.5" y2="13" stroke="#fff" stroke-width="1.2"/>
          </svg>
          www.velmorasys.example
        </li>
      </ul>
    </div>
  </section>
</body>
</html>
```